Print materials for 3-star hotel

We are changing up our print materials (notepads, letterheads, key card jackets, small flyer for the room rates) We are a 3 star business hotel in the Philippines and have mainly used grey tones and clean, simple lines. See attached photos for logo and hotel interior photos.

Target Market(s)

Business

Contact Information for Business Card

Corvale Terrace Hotel
Lindwell Banca Avenue corner Tolenta St Cebu City 6000 Philippines
Tel: +63 32 481 7302
Mobile: +63 917 648 2095
www.corvaleterracehotel.example

Font styles to use
Serif
Sans Serif

Requirements
Must have
• Simple
• Readable font and font size
Nice to have
• Neutral colors, grey and taupes
Should not have
• No purples and bright blues

```html
<!DOCTYPE html>
<html lang="en">
<head>
<meta charset="utf-8">
<title>Corvale Terrace Hotel – Business Card</title>
<link rel="stylesheet" href="https://fonts.googleapis.com/css2?family=Cinzel:wght@400;500&family=Roboto:wght@400;500&display=swap">
<style>
  :root {
    --backdrop: #2b2b2d;
    --card: #1d1d1f;
    --foil: #d9c9ae;
    --foil-soft: #c9b898;
  }
  * { margin: 0; padding: 0; box-sizing: border-box; }
  html, body {
    width: 1200px;
    height: 900px;
    overflow: hidden;
    background: var(--backdrop);
  }
  .sheet {
    width: 1200px;
    height: 900px;
    display: flex;
    flex-direction: column;
    align-items: center;
    justify-content: center;
    gap: 40px;
  }
  .card {
    position: relative;
    width: 640px;
    height: 366px;
    background: var(--card);
    box-shadow: 0 10px 28px rgba(0,0,0,0.45);
    color: var(--foil);
  }
  .card__frame {
    position: absolute;
    inset: 14px;
    border: 2px solid var(--foil);
  }
  .card__content {
    position: absolute;
    inset: 0;
    display: flex;
    flex-direction: column;
    align-items: center;
    justify-content: center;
    text-align: center;
  }

  /* Front */
  .brand__mark {
    width: 46px;
    height: 46px;
    background: var(--foil);
    margin-bottom: 18px;
  }
  .brand__name {
    font-family: "Cinzel", serif;
    font-weight: 400;
    font-size: 27px;
    letter-spacing: 4px;
    line-height: 1;
    color: var(--foil);
  }
  .brand__type {
    font-family: "Cinzel", serif;
    font-weight: 400;
    font-size: 15px;
    letter-spacing: 6px;
    line-height: 1;
    margin-top: 6px;
    color: var(--foil);
  }

  /* Back */
  .contact__name {
    font-family: "Cinzel", serif;
    font-weight: 500;
    font-size: 25px;
    letter-spacing: 1.5px;
    line-height: 1.1;
  }
  .contact__role {
    font-family: "Roboto", sans-serif;
    font-weight: 500;
    font-size: 15px;
    margin-top: 2px;
  }
  .contact__rule {
    width: 44px;
    height: 2px;
    background: var(--foil-soft);
    margin: 14px 0;
  }
  .contact__lines {
    font-family: "Roboto", sans-serif;
    font-weight: 400;
    font-size: 16px;
    line-height: 1.3;
  }
</style>
</head>
<body>
  <main class="sheet">
    <section class="card card--front">
      <div class="card__frame"></div>
      <div class="card__content brand">
        <div class="brand__mark"></div>
        <p class="brand__name">Corvale Terrace</p>
        <p class="brand__type">Hotel</p>
      </div>
    </section>

    <section class="card card--back">
      <div class="card__frame"></div>
      <div class="card__content contact">
        <h1 class="contact__name">ELIAS MONTERO</h1>
        <p class="contact__role">CEO/Founder</p>
        <div class="contact__rule"></div>
        <address class="contact__lines" style="font-style: normal;">
          2140 Larkfield Road<br>
          Talisay, Cebu 6045
        </address>
        <div class="contact__rule"></div>
        <p class="contact__lines">
          +63 32 481 7302<br>
          elias@corvaleterrace.example<br>
          www.corvaleterracehotel.example
        </p>
      </div>
    </section>
  </main>
</body>
</html>
```